Ridgeline Journeys business card

please see website
www.ridgelinejourneys.comau

info needed on card
Curtis Halvey
Ph
email
Adventure Riding GPS trails

please use my logo and colours off my site

Curtis Halvey
curtis@ridgelinejourneys.com

```html
<!DOCTYPE html>
<html lang="en">
<head>
<meta charset="utf-8">
<title>Ridgeline Journeys – Business Card</title>
<link href="https://fonts.googleapis.com/css2?family=Open+Sans:wght@400;600;800&display=swap" rel="stylesheet">
<style>
  :root {
    --page-bg: #e6e6e6;
    --card-bg: #ffffff;
    --card-back-bg: #f7f7f7;
    --ink: #161616;
    --ink-soft: #2a2a2a;
    --brand-yellow: #f5c800;
    --faint-mark: #ecebe4;
    --card-shadow: rgba(0, 0, 0, 0.18);
  }
  * { box-sizing: border-box; margin: 0; padding: 0; }
  html, body {
    width: 1200px; height: 864px; overflow: hidden;
    background: var(--page-bg);
    font-family: "Open Sans", Arial, sans-serif;
  }
  .card {
    position: absolute;
    left: 300px;
    width: 600px; height: 343px;
    border-radius: 3px;
    box-shadow: 0 6px 18px var(--card-shadow);
    overflow: hidden;
  }
  .card--front { top: 40px; background: var(--card-bg); }
  .card--back  { top: 460px; background: var(--card-back-bg); }

  /* Front */
  .front-brand {
    position: absolute; left: 118px; top: 92px;
    display: flex; align-items: center; gap: 26px;
  }
  .brand-dot {
    width: 86px; height: 86px; border-radius: 50%;
    background: var(--brand-yellow);
    flex: none;
  }
  .brand-name {
    font-weight: 800; color: var(--ink);
    text-transform: uppercase; line-height: 1.02;
    font-size: 36px; letter-spacing: 0.5px;
  }
  .tagline {
    position: absolute; left: 0; right: 0; top: 218px;
    text-align: center;
    font-weight: 600; font-size: 14px; letter-spacing: 1px;
    color: var(--ink);
  }

  /* Back */
  .back-mark {
    position: absolute; right: -90px; top: 40px;
    width: 360px; height: 360px; border-radius: 50%;
    background: var(--faint-mark);
  }
  .back-brand {
    position: absolute; left: 34px; top: 30px;
    font-size: 32px;
  }
  .holder-name {
    position: absolute; left: 40px; top: 168px;
    font-weight: 600; font-size: 17px;
    color: var(--brand-yellow);
  }
  .contact-list {
    position: absolute; left: 40px; top: 208px;
    list-style: none;
  }
  .contact-item {
    display: flex; align-items: center; gap: 8px;
    font-size: 14px; color: var(--ink-soft);
    margin-bottom: 7px;
  }
  .contact-icon {
    width: 16px; height: 14px; border-radius: 2px;
    background: var(--brand-yellow);
    display: flex; align-items: center; justify-content: center;
    flex: none;
  }
</style>
</head>
<body>

<section class="card card--front" aria-label="Card front">
  <div class="front-brand">
    <span class="brand-dot"></span>
    <div class="brand-name">Ridgeline<br>Journeys</div>
  </div>
  <p class="tagline">ADVENTURE RIDING GPS TRAILS</p>
</section>

<section class="card card--back" aria-label="Card back">
  <span class="back-mark"></span>
  <div class="brand-name back-brand">Ridgeline<br>Journeys</div>
  <p class="holder-name">Curtis Halvey</p>
  <ul class="contact-list">
    <li class="contact-item">
      <span class="contact-icon">
        <svg width="10" height="9" viewBox="0 0 10 9"><path d="M1 1.5 Q5 -0.5 9 1.5 L8 3.2 L6.5 2.6 L6.5 1.8 Q5 1.3 3.5 1.8 L3.5 2.6 L2 3.2 Z M2.5 4 H7.5 L8.5 8 H1.5 Z" fill="#222"/></svg>
      </span>
      (044)-555-0182
    </li>
    <li class="contact-item">
      <span class="contact-icon">
        <svg width="10" height="8" viewBox="0 0 10 8"><rect x="0.5" y="0.5" width="9" height="7" fill="#222"/><path d="M0.8 1 L5 4.5 L9.2 1" stroke="#f5c800" stroke-width="1" fill="none"/></svg>
      </span>
      curtis@ridgelinejourneys.com
    </li>
    <li class="contact-item">
      <span class="contact-icon">
        <svg width="10" height="10" viewBox="0 0 10 10"><path d="M4 6 L6 4 M3.2 5 L1.8 6.4 a1.4 1.4 0 0 0 1.9 1.9 L5 7 M5 3 L6.4 1.7 a1.4 1.4 0 0 1 1.9 1.9 L7 5" stroke="#222" stroke-width="1.3" fill="none" stroke-linecap="round"/></svg>
      </span>
      www.ridgelinejourneys.com
    </li>
  </ul>
</section>

</body>
</html>
```